Printed Circuit Board Company Web Site Design - Please see new file 82012 web design

We are a printed circuit board manufacturer. Need a company professional web site to allow our potential customers to know more about our background, capability and our products. The web site will contain three languages, which are Chinese, English and Japanese. Our audience are mainly electronic companies that procure printed circuit boards. I have a word document that have all the required text in all three languages. The final design should communicate the impression that we embrace quality, trustworthiness and long term partnership business principles.
We should have sections that allow us to post pictures of our facilities.
I have added the three files in three different languages.
Some of the information is below:
Background
RDV Harbourline Limited (RDV) was set up in Hong Kong in 2007 by two Hong Kong entrepreneurs, Mr. Tak Wong and Mr. Lok Fai. We acquired the single sided printed circuit board factory located in Dongguan City, Guangdong Province, China, from Tovand Corporation of the U.S. in 2007. In addition to RDV, Mr. Wong and Mr. Fai also own Halberd Technology Company Limited, a semiconductor company based in Hong Kong since 1997 with a total investment of over US$100 million. Halberd is engaged in the manufacturing of flexible substrates and MEMS assembly business.
RDV has been awarded TS 16949 and ISO14000 certificates since 2009 and 2004 respectively.
Business Principles
RDV Harbourline Limited strives to be a professional top notched printed circuit board supplier. We embrace four “EXCELLENCE” principles, namely, excellence in quality, excellence in prices, excellence in services and excellence in on time delivery.
We approach each customer with a long-term partnership view that delivers the lowest ownership costs and highest total values to our customers. We customize quotations and solutions in order to allow our customers to win more businesses. We believe by thinking from our customers’ points of view we will be able to create a WIN-WIN relationship.
Customers
Due to our excellent quality, services and production systems, RDV Harbourline Limited manage to service a number of large Japanese and US customers, which include:
Technical capability overview
Below is an overview of our current capability:
Target Market(s)
Electronic companies buyers
Industry/Entity Type
Business
Requirements
Must have
- Capability description
Should not have
- no cartoon

```html
<!DOCTYPE html>
<html lang="en">
<head>
<meta charset="utf-8">
<title>RDV Harbourline Limited</title>
<link href="https://fonts.googleapis.com/css2?family=Source+Sans+3:wght@400;600;700&display=swap" rel="stylesheet">
<style>
:root{
  --green:#0b6e4f;
  --green-dark:#075a3f;
  --text:#333;
  --muted:#555;
  --rule:#d6d6d6;
  --panel-top:#ffffff;
  --panel-bottom:#e3e3e3;
  --footer:#efefef;
  --badge:#fafafa;
  --badge-line:#c8c8c8;
}
*{box-sizing:border-box;margin:0;padding:0}
html,body{width:847px;height:1200px;overflow:hidden;background:#fff}
body{position:relative;font-family:"Source Sans 3",Arial,sans-serif;color:var(--text)}
.abs{position:absolute}
.brand{left:92px;top:20px;font-size:22px;font-weight:700;color:var(--green);line-height:1.05;width:200px}
.phone{left:620px;top:50px;display:flex;align-items:center;gap:10px;font-size:13px;color:#222}
.nav{left:0;top:82px;width:847px;height:35px;background:linear-gradient(#fafafa,#d8d8d8);border-top:1px solid #ccc;border-bottom:1px solid #bbb}
.nav ul{list-style:none;position:absolute;left:92px;top:0;height:35px;display:flex}
.nav li{height:35px;display:flex;align-items:center;justify-content:center;border-left:1px solid #a9a9a9;font-size:12px;color:#222}
.nav li:last-child{border-right:1px solid #a9a9a9}
.nav li.active{color:var(--green)}
.hero{left:0;top:117px;width:847px;height:319px;background:linear-gradient(100deg,#6b4a3a 0%,#9a8b7d 30%,#3c3a38 50%,#b8a86a 75%,#7a6f55 100%)}
.section-title{font-size:17px;color:var(--green);font-weight:400}
.about-title{left:92px;top:454px}
.about-photo{left:92px;top:483px;width:112px;height:67px;background:linear-gradient(135deg,#5b6470,#a9b0bb);border-radius:2px}
.about-text{left:232px;top:479px;width:523px;font-size:8.3px;line-height:16.3px;color:#333}
.read-more{left:655px;top:540px;width:100px;text-align:right;font-size:9.5px;color:var(--green)}
.rule{left:92px;width:663px;height:1px;background:var(--rule)}
.panel{top:592px;height:146px;background:linear-gradient(var(--panel-top),var(--panel-bottom));border-radius:2px;padding:12px 11px}
.panel h3{font-size:13.5px;font-weight:400;color:var(--green);margin-bottom:9px}
.panel ul{list-style:none}
.panel li{font-size:9.5px;height:16.8px;display:flex;align-items:center;gap:11px;color:#222;padding-left:1px}
.tick{width:8px;height:8px;flex:none}
.join-title{left:92px;top:776px}
.join-sub{left:149px;top:785px;font-size:8px;color:#333}
.feature{display:flex;gap:12px}
.feature .icon{width:32px;height:42px;border-radius:5px;flex:none}
.feature h4{font-size:10px;font-weight:400;color:#111;margin-bottom:2px}
.feature p{font-size:8px;line-height:16px;color:#555;width:140px}
.feature.link h4{color:var(--green)}
.order-input{left:369px;top:824px;width:100px;height:19px;background:linear-gradient(#f4f4f4,#dcdcdc);border:1px solid #c4c4c4;border-radius:2px;font-size:8px;color:#555;padding:4px 6px}
.btn{top:805px;width:98px;height:28px;border-radius:3px;display:flex;align-items:center;justify-content:center;font-size:12px;font-weight:700;color:#fff}
.btn-signup{left:521px;background:linear-gradient(#10956a,var(--green-dark));border:1px solid #054a33}
.btn-login{left:657px;background:linear-gradient(#d2d2d2,#a9a9a9);border:1px solid #9a9a9a}
.ticket{left:520px;top:855px;width:235px;height:54px;background:linear-gradient(#fafafa,#e6e6e6);border:1px solid #c4c4c4;border-radius:2px;display:flex;gap:12px;padding:4px 8px}
.ticket .icon{width:40px;height:44px;background:linear-gradient(#e9eef6,#b9c9e0);border:1px solid #9aa8bd;flex:none}
.ticket h4{font-size:9.5px;font-weight:400;color:var(--green);margin-bottom:1px}
.ticket p{font-size:7.8px;line-height:15.5px;color:#666}
.customers-title{left:0;top:948px;width:847px;text-align:center}
.customer{top:982px;height:38px;display:flex;align-items:center;gap:8px;font-size:26px;font-weight:700;color:#2b2b2b}
.customer .dot{width:30px;height:30px;border-radius:50%;background:#8a8a8a;flex:none}
.footer{left:0;top:1043px;width:847px;height:157px;background:var(--footer)}
.footer-links{position:absolute;top:22px;left:0;width:847px;display:flex;justify-content:center;font-size:9px;color:#333}
.footer-links span{padding:0 13px;border-left:1px solid #777;line-height:11px}
.footer-links span:first-child{border-left:none}
.copyright{position:absolute;top:45px;left:0;width:847px;text-align:center;font-size:9px;color:#444}
.privacy{position:absolute;top:64px;left:0;width:847px;text-align:center;font-size:9px;color:#666}
.pay{position:absolute;top:107px;height:38px;border-radius:3px;display:flex;align-items:center;justify-content:center;font-size:9.5px;font-weight:600;background:var(--badge);border:1px solid var(--badge-line);color:var(--text)}
</style>
</head>
<body>

<header>
  <div class="abs brand">RDV Harbourline Limited</div>
  <div class="abs phone">
    <svg width="25" height="17" viewBox="0 0 25 17" aria-hidden="true"><path d="M2 6 Q12.5-2 23 6 L21 9 L17 7.5 L17 5 Q12.5 3.5 8 5 L8 7.5 L4 9 Z" fill="var(--green)"/><rect x="5" y="9" width="15" height="8" rx="1.5" fill="var(--green)"/><circle cx="12.5" cy="13" r="2.2" fill="#fff"/></svg>
    <span>(86)755-204318862</span>
  </div>
  <nav class="abs nav">
    <ul>
      <li class="active" style="width:61px">Home</li>
      <li style="width:92px">Capabilities</li>
      <li style="width:129px">Support &amp; Resource</li>
      <li style="width:100px">Quick Quote</li>
      <li style="width:76px">About Us</li>
      <li style="width:84px">Contact Us</li>
      <li style="width:121px">knowledge Center</li>
    </ul>
  </nav>
</header>

<div class="abs hero" role="img" aria-label="Factory worker sorting electronic components beside a circuit board on an assembly line"></div>

<main>
  <h2 class="abs section-title about-title">About Us</h2>
  <div class="abs about-photo" role="img" aria-label="Operator working at a circuit board production machine"></div>
  <p class="abs about-text">Lorem ipsum dolor sit amet, consectetur adipiscing elit. Fusce accumsan, elit a suscipit sagittis, tortor sapien cursus risus, non rhoncus lectus nunc ac nulla?Aliquam molestie, mi et imperdiet euismod, dui purus auctor tellus, et interdum lacus lectus et ante. Sed accumsan sollicitudin sapien, sit amet adipiscing turpis gravida ac. In congue, neque ac lobortis volutpat, libero mauris varius mi, vitae suscipit ipsum ligula vitae risus. Duis aliquam nibh a</p>
  <a class="abs read-more">Read More &gt;&gt;&gt;</a>
  <div class="abs rule" style="top:568px"></div>

  <section class="abs panel" style="left:92px;width:211px">
    <h3>PCB and SMT Capacity</h3>
    <ul>
      <li><svg class="tick" viewBox="0 0 8 8"><circle cx="4" cy="4" r="4" fill="var(--green)"/><path d="M2.2 4.1 3.5 5.3 5.9 2.8" stroke="#fff" stroke-width="1.1" fill="none"/></svg>Rigid PCB Capacity</li>
      <li><svg class="tick" viewBox="0 0 8 8"><circle cx="4" cy="4" r="4" fill="var(--green)"/><path d="M2.2 4.1 3.5 5.3 5.9 2.8" stroke="#fff" stroke-width="1.1" fill="none"/></svg>Flex PCB Capacity</li>
      <li><svg class="tick" viewBox="0 0 8 8"><circle cx="4" cy="4" r="4" fill="var(--green)"/><path d="M2.2 4.1 3.5 5.3 5.9 2.8" stroke="#fff" stroke-width="1.1" fill="none"/></svg>Metal Core PCB Capacity</li>
      <li><svg class="tick" viewBox="0 0 8 8"><circle cx="4" cy="4" r="4" fill="var(--green)"/><path d="M2.2 4.1 3.5 5.3 5.9 2.8" stroke="#fff" stroke-width="1.1" fill="none"/></svg>PCB Assembly Capacity</li>
      <li><svg class="tick" viewBox="0 0 8 8"><circle cx="4" cy="4" r="4" fill="var(--green)"/><path d="M2.2 4.1 3.5 5.3 5.9 2.8" stroke="#fff" stroke-width="1.1" fill="none"/></svg>PCB Equipment</li>
      <li><svg class="tick" viewBox="0 0 8 8"><circle cx="4" cy="4" r="4" fill="var(--green)"/><path d="M2.2 4.1 3.5 5.3 5.9 2.8" stroke="#fff" stroke-width="1.1" fill="none"/></svg>PCB Assembly Equipment</li>
    </ul>
  </section>
  <section class="abs panel" style="left:318px;width:212px">
    <h3>Quality Control System</h3>
    <ul>
      <li><svg class="tick" viewBox="0 0 8 8"><circle cx="4" cy="4" r="4" fill="var(--green)"/><path d="M2.2 4.1 3.5 5.3 5.9 2.8" stroke="#fff" stroke-width="1.1" fill="none"/></svg>PCB Quality Control System</li>
      <li><svg class="tick" viewBox="0 0 8 8"><circle cx="4" cy="4" r="4" fill="var(--green)"/><path d="M2.2 4.1 3.5 5.3 5.9 2.8" stroke="#fff" stroke-width="1.1" fill="none"/></svg>PCB Assembly Quality Control System</li>
      <li><svg class="tick" viewBox="0 0 8 8"><circle cx="4" cy="4" r="4" fill="var(--green)"/><path d="M2.2 4.1 3.5 5.3 5.9 2.8" stroke="#fff" stroke-width="1.1" fill="none"/></svg>PCB/PCBA Quanlity Control Equipment</li>
      <li><svg class="tick" viewBox="0 0 8 8"><circle cx="4" cy="4" r="4" fill="var(--green)"/><path d="M2.2 4.1 3.5 5.3 5.9 2.8" stroke="#fff" stroke-width="1.1" fill="none"/></svg>Our Certificates</li>
      <li><svg class="tick" viewBox="0 0 8 8"><circle cx="4" cy="4" r="4" fill="var(--green)"/><path d="M2.2 4.1 3.5 5.3 5.9 2.8" stroke="#fff" stroke-width="1.1" fill="none"/></svg>Our Awards</li>
      <li><svg class="tick" viewBox="0 0 8 8"><circle cx="4" cy="4" r="4" fill="var(--green)"/><path d="M2.2 4.1 3.5 5.3 5.9 2.8" stroke="#fff" stroke-width="1.1" fill="none"/></svg>90 Days Limited Warranty</li>
    </ul>
  </section>
  <section class="abs panel" style="left:543px;width:212px">
    <h3>Products/Service</h3>
    <ul>
      <li><svg class="tick" viewBox="0 0 8 8"><circle cx="4" cy="4" r="4" fill="var(--green)"/><path d="M2.2 4.1 3.5 5.3 5.9 2.8" stroke="#fff" stroke-width="1.1" fill="none"/></svg>OEM Service</li>
      <li><svg class="tick" viewBox="0 0 8 8"><circle cx="4" cy="4" r="4" fill="var(--green)"/><path d="M2.2 4.1 3.5 5.3 5.9 2.8" stroke="#fff" stroke-width="1.1" fill="none"/></svg>PCB Fabrication</li>
      <li><svg class="tick" viewBox="0 0 8 8"><circle cx="4" cy="4" r="4" fill="var(--green)"/><path d="M2.2 4.1 3.5 5.3 5.9 2.8" stroke="#fff" stroke-width="1.1" fill="none"/></svg>PCB Assembly</li>
      <li><svg class="tick" viewBox="0 0 8 8"><circle cx="4" cy="4" r="4" fill="var(--green)"/><path d="M2.2 4.1 3.5 5.3 5.9 2.8" stroke="#fff" stroke-width="1.1" fill="none"/></svg>FAQ</li>
      <li><svg class="tick" viewBox="0 0 8 8"><circle cx="4" cy="4" r="4" fill="var(--green)"/><path d="M2.2 4.1 3.5 5.3 5.9 2.8" stroke="#fff" stroke-width="1.1" fill="none"/></svg>Knowledge Center</li>
      <li><svg class="tick" viewBox="0 0 8 8"><circle cx="4" cy="4" r="4" fill="var(--green)"/><path d="M2.2 4.1 3.5 5.3 5.9 2.8" stroke="#fff" stroke-width="1.1" fill="none"/></svg>Downloads</li>
    </ul>
  </section>

  <div class="abs rule" style="top:758px"></div>

  <h2 class="abs section-title join-title">Join Us</h2>
  <span class="abs join-sub">Silver Crane Will Help You</span>

  <div class="abs feature" style="left:92px;top:803px">
    <div class="icon" role="img" aria-label="Calculator icon" style="background:linear-gradient(#6c6c6c,#2a2a2a)"></div>
    <div><h4>Online Quote</h4><p>Receive your PCB and PCB assembly quote instantly</p></div>
  </div>
  <div class="abs feature" style="left:92px;top:867px">
    <div class="icon" role="img" aria-label="Order form icon" style="background:linear-gradient(#f2efd8,#9bb36a);height:36px"></div>
    <div><h4>Place Order</h4><p>Place PCB and PCB assembly orders in a few clicks</p></div>
  </div>
  <div class="abs feature link" style="left:318px;top:803px">
    <div class="icon" role="img" aria-label="Globe with cursor icon" style="background:radial-gradient(circle at 40% 40%,#8fd0f0,#2a7fb0);border-radius:50%;width:40px;height:40px"></div>
    <div><h4>Track Your Orders</h4></div>
  </div>
  <div class="abs order-input">Order No.
    <svg width="10" height="10" viewBox="0 0 10 10" style="position:absolute;right:6px;top:4px"><circle cx="4" cy="4" r="3" stroke="var(--green)" stroke-width="1.5" fill="none"/><path d="M6.2 6.2 9 9" stroke="var(--green)" stroke-width="1.8"/></svg>
  </div>
  <div class="abs feature link" style="left:318px;top:867px">
    <div class="icon" role="img" aria-label="Satellite dish icon" style="background:radial-gradient(circle at 40% 50%,#f0f0f0,#a8a8a8);border-radius:50%;width:40px;height:40px"></div>
    <div><h4>Support</h4><p style="color:#555">Answer your PCB and PCB assembly questions 24/7</p></div>
  </div>

  <a class="abs btn btn-signup">SIGN UP FREE</a>
  <a class="abs btn btn-login">SECURE LOGIN</a>

  <div class="abs ticket">
    <div class="icon" role="img" aria-label="Support ticket document icon"></div>
    <div><h4>Start &nbsp;A Ticket</h4><p>If you have any questions, you can use the ticket system to contact our team for help</p></div>
  </div>

  <div class="abs rule" style="top:934px"></div>

  <h2 class="abs section-title customers-title">Our Customer</h2>
  <div class="abs customer" style="left:92px"><span class="dot"></span>Veltrana</div>
  <div class="abs customer" style="left:272px">Norvexa</div>
  <div class="abs customer" style="left:467px"><span class="dot"></span>Kiroda</div>
  <div class="abs customer" style="left:614px"><span class="dot"></span>Tamsen</div>
</main>

<footer class="abs footer">
  <div class="footer-links">
    <span>Quality Control System</span><span>Products/Service</span><span>Success Stories</span><span>Friendly Links</span>
  </div>
  <p class="copyright">Copyright © 2012 Harbourline Boards Limited</p>
  <p class="privacy">All Privacy / Policy</p>
  <div class="pay" style="left:262px;width:60px">Credit Card</div>
  <div class="pay" style="left:353px;width:60px">Tallyway</div>
  <div class="pay" style="left:448px;width:50px">Cardiva</div>
  <div class="pay" style="left:531px;width:55px">Bank Card</div>
</footer>

</body>
</html>
```